Financial Services General Marketing Brochure

Need a brochure to help recipients understand what makes BWC unique and the services that we offer. Must match look/feel of website https://brightwellcustody.example Layouts should make it easy to read the content - content should not be crammed into a traditional size/layout. Please see attached creative brief for specifics.

Target Market(s)

Financial advisors and mature couples looking for trustee services.

Industry/Entity Type

Financial Service

Colors
34a7d8
ffc214

Requirements
Must have
• See Creative Brief

```html
<!DOCTYPE html>
<html lang="en">
<head>
<meta charset="utf-8">
<title>Brightwell Custody Brochure</title>
<link href="https://fonts.googleapis.com/css2?family=Baloo+2:wght@500;600;700&family=Libre+Baskerville&family=Quicksand:wght@400;500;600&display=swap" rel="stylesheet">
<style>
:root{
  --blue:#3d6a91;
  --blue-band:rgba(58,104,145,.86);
  --beige:#e7e2d9;
  --cream:#f7f1e6;
  --gold:#f0b42b;
  --leaf:#f1a223;
  --ink:#2f3b46;
  --white:#ffffff;
  --bg:#e4e4e6;
}
*{box-sizing:border-box;margin:0;padding:0}
html,body{width:857px;height:1200px;overflow:hidden;background:var(--bg)}
body{position:relative;font-family:"Quicksand",sans-serif;color:var(--ink)}
.spread{position:absolute;left:20px;width:817px;height:550px;display:flex;box-shadow:0 6px 18px rgba(0,0,0,.18)}
.spread--outer{top:20px}
.spread--inner{top:625px}
.page{position:relative;width:408.5px;height:550px;overflow:hidden}

/* back panel */
.services{background:var(--beige);padding:30px 30px 20px 34px}
.services__title{font-family:"Libre Baskerville",serif;color:var(--blue);font-size:24px;letter-spacing:.5px;margin-bottom:6px}
.services h3{font-family:"Baloo 2",sans-serif;color:var(--blue);font-size:14px;font-weight:600;line-height:1.1;margin-top:9px}
.services p,.services li{font-size:10.5px;line-height:1.35;font-style:italic}
.services ul{list-style:none}
.services li::before{content:"✓";color:var(--blue);font-weight:700;margin-right:3px;font-style:normal}
.services hr{border:0;border-top:1px solid var(--blue);width:120px;margin-top:7px}
.services__foot{position:absolute;left:34px;bottom:24px;display:flex;gap:22px;align-items:flex-end}
.brand{display:flex;align-items:center;gap:6px;font-family:"Baloo 2",sans-serif;font-weight:600;color:var(--blue);font-size:15px;line-height:1}
.brand__dot{width:14px;height:14px;border-radius:50%;background:var(--leaf)}
.contact{font-size:10px;line-height:1.5;font-style:italic;border-top:1px solid var(--blue);padding-top:5px}

/* cover */
.cover__photo{position:absolute;inset:0;background:linear-gradient(160deg,#d8dcd6 0%,#b9ae8e 35%,#8d6c43 60%,#c7b08a 80%,#e6ddc9 100%)}
.cover__band{position:absolute;left:0;right:0;top:300px;bottom:26px;background:var(--blue-band);padding:46px 20px 0;text-align:center;color:var(--white)}
.cover__leaves{position:absolute;left:0;right:0;bottom:0;height:26px;background:linear-gradient(90deg,#a0612a,#d7a65a,#8a4e22,#c98a3c)}
.cover__headline{font-family:"Libre Baskerville",serif;font-size:14.5px;font-weight:400;line-height:1.45;letter-spacing:.6px;white-space:nowrap}
.cover .brand{color:var(--white);justify-content:center;margin-top:30px;font-size:20px}

/* inner left */
.intro{position:absolute;left:0;top:0;width:100%;height:255px;background:var(--blue);color:var(--white);padding:22px 150px 0 24px}
.intro p{font-size:10.5px;line-height:1.4;margin-bottom:10px;text-align:justify}
.intro__photo{position:absolute;right:0;top:40px;width:130px;height:215px;background:linear-gradient(160deg,#c48a4a,#4c3a32 55%,#1f2a3b)}
.intro__caption{position:absolute;right:10px;bottom:8px;color:var(--white);font-size:9.5px;text-align:right;line-height:1.3}
.unique{position:absolute;left:0;top:255px;width:100%;height:295px;background:linear-gradient(90deg,var(--gold),#f2c357);padding:16px 22px}
.unique__title{font-family:"Baloo 2",sans-serif;font-weight:700;color:var(--blue);font-size:23px;line-height:1.1;margin-bottom:6px}
.unique h4{font-family:"Baloo 2",sans-serif;font-weight:600;color:var(--blue);font-size:12.5px;line-height:1.1;margin-top:7px}
.unique p{font-size:9.5px;line-height:1.3;max-width:320px;padding-bottom:4px;border-bottom:1px solid rgba(61,106,145,.45)}
.unique p:last-child{border-bottom:0}

/* inner right */
.team{background:var(--cream)}
.team svg{display:block}
.node-label{font-family:"Baloo 2",sans-serif;font-weight:600;fill:var(--blue);font-size:13px;text-anchor:middle}
.node-sub{font-family:"Libre Baskerville",serif;fill:var(--ink);font-size:5.5px;text-anchor:middle}
.photo-label{font-family:"Quicksand",sans-serif;font-weight:600;fill:var(--white);font-size:7.5px;text-anchor:middle}
.team-title{font-family:"Baloo 2",sans-serif;font-weight:600;fill:var(--blue);font-size:17px;text-anchor:middle}
</style>
</head>
<body>

<section class="spread spread--outer">
  <div class="page services">
    <h1 class="services__title">OUR SERVICES</h1>
    <h3>What We Offer</h3>
    <p>We specialize exclusively in the delivery of trustee and estate fiduciary services.</p>
    <hr>
    <h3>Who We Serve</h3>
    <p>Families<br>Professional Advisors<br>Foundations</p>
    <hr>
    <h3>How We Serve</h3>
    <p>Our expertise and experience is in family wealth. In this regard, we serve in the following ways:</p>
    <ul>
      <li>Trustee (Trusts)</li>
      <li>Executor and Personal Representative (Will)</li>
      <li>Agent for Financial Affairs (Power of Attorney)</li>
      <li>Trust Protector</li>
      <li>Special Independent Trustee</li>
      <li>Consultant</li>
      <li>Expert Witness</li>
    </ul>
    <hr>
    <h3>Trust Specialties</h3>
    <p>The general types of trusts on which we serve as trustee:</p>
    <ul>
      <li>Family Trusts</li>
      <li>Charitable Trusts</li>
      <li>Family Foundations</li>
      <li>Life Insurance Trusts</li>
      <li>Retirement Trusts</li>
      <li>Special Needs Trusts</li>
    </ul>
    <div class="services__foot">
      <div class="brand"><span class="brand__dot"></span>Brightwell Custody</div>
      <div class="contact">brightwellcustody.example<br>555-014-2280<br>info@brightwellcustody.example</div>
    </div>
  </div>

  <div class="page cover">
    <div class="cover__photo" role="img" aria-label="Three generations of a family running hand in hand through an autumn park"></div>
    <div class="cover__band">
      <h2 class="cover__headline">HELPING FAMILIES PROTECT<br>AND ENRICH A<br>MULTI-GENERATIONAL HERITAGE</h2>
      <div class="brand"><span class="brand__dot"></span>Brightwell Custody</div>
    </div>
    <div class="cover__leaves" role="img" aria-label="Strip of fallen autumn leaves"></div>
  </div>
</section>

<section class="spread spread--inner">
  <div class="page">
    <div class="intro">
      <p>We understand that wealth and families is very complex. As families try to transfer wealth it can be an incredible blessing or, if done improperly, can be incredibly destructive. Often a neutral third party is needed to come alongside the family's advisory team to provide guidance as families go through their wealth transition.</p>
      <p>Our relational focus and Open Framework approach helps families to successfully navigate through the complexities of wealth, family and trusts. We believe a family "legacy" is about more than just money.</p>
      <div class="intro__photo" role="img" aria-label="Portrait of the founding principal in a suit"></div>
      <div class="intro__caption">Daniel Hart, J.D.<br>Founding Principal</div>
    </div>
    <div class="unique" role="region" aria-label="What makes BWC unique">
      <h2 class="unique__title">What Makes BWC Unique?</h2>
      <h4>1. Responsive</h4>
      <p>The family deals directly with decision makers instead of being subject to committees with whom the family may never have the opportunity to interact or engage.</p>
      <h4>2. Family Focus</h4>
      <p>We help families successfully navigate the complexities of family wealth, not just perform trust administration.</p>
      <h4>3. Independent</h4>
      <p>To avoid any conflicts of interest, we have no formal affiliations with wealth management firms or financial advisory practices.</p>
      <h4>4. Customized</h4>
      <p>Together we develop a customized approach that will best suit the family's needs.</p>
      <h4>5. Collaborative</h4>
      <p>We work collaboratively with the family's team of trusted professionals.</p>
    </div>
  </div>

  <div class="page team">
    <svg width="408" height="550" viewBox="0 0 408 550">
      <defs>
        <linearGradient id="skin-a" x1="0" y1="0" x2="1" y2="1"><stop offset="0" stop-color="#5a3b2a"/><stop offset="1" stop-color="#d8a487"/></linearGradient>
        <linearGradient id="skin-b" x1="0" y1="0" x2="1" y2="1"><stop offset="0" stop-color="#f1dbcf"/><stop offset="1" stop-color="#c9a391"/></linearGradient>
        <linearGradient id="skin-c" x1="0" y1="0" x2="1" y2="1"><stop offset="0" stop-color="#e9ecef"/><stop offset="1" stop-color="#b89a87"/></linearGradient>
        <filter id="lift" x="-20%" y="-20%" width="150%" height="150%"><feDropShadow dx="4" dy="5" stdDeviation="3" flood-color="#5d7890" flood-opacity=".55"/></filter>
      </defs>
      <text class="team-title" x="204" y="48">Brightwell Custody</text>
      <text class="team-title" x="204" y="70">Client/Family Centered Team</text>

      <g stroke="#9a8f80" stroke-width="1.2">
        <line x1="200" y1="300" x2="130" y2="180"/>
        <line x1="200" y1="300" x2="255" y2="150"/>
        <line x1="200" y1="300" x2="335" y2="230"/>
        <line x1="200" y1="300" x2="340" y2="375"/>
        <line x1="200" y1="300" x2="300" y2="470"/>
        <line x1="200" y1="300" x2="190" y2="450"/>
        <line x1="200" y1="300" x2="80" y2="335"/>
      </g>

      <g filter="url(#lift)">
        <g role="img" aria-label="Photo of the current beneficiary, a smiling young woman">
          <circle cx="130" cy="180" r="50" fill="url(#skin-a)" stroke="#d6c9b2" stroke-width="3"/>
        </g>
        <g role="img" aria-label="Photo of the future beneficiaries, two young children">
          <circle cx="255" cy="150" r="45" fill="url(#skin-b)" stroke="#d6c9b2" stroke-width="3"/>
        </g>
        <circle cx="335" cy="230" r="47" fill="var(--white)" stroke="#d6c9b2" stroke-width="3"/>
        <circle cx="340" cy="375" r="47" fill="var(--white)" stroke="#d6c9b2" stroke-width="3"/>
        <circle cx="300" cy="470" r="46" fill="var(--white)" stroke="#d6c9b2" stroke-width="3"/>
        <circle cx="190" cy="450" r="47" fill="var(--white)" stroke="#d6c9b2" stroke-width="3"/>
        <circle cx="80" cy="335" r="47" fill="var(--white)" stroke="#d6c9b2" stroke-width="3"/>
        <g role="img" aria-label="Photo of the trust creators, a smiling older couple">
          <polygon points="200,232 268,275 250,360 150,360 132,275" fill="url(#skin-c)" stroke="#d6c9b2" stroke-width="3"/>
        </g>
      </g>

      <text class="photo-label" x="130" y="218">Current Beneficiary</text>
      <text class="photo-label" x="255" y="183">Future Beneficiary</text>
      <text class="node-label" x="200" y="352" style="fill:#f5f0e6">Trust Creator</text>
      <text class="node-label" x="335" y="235">Accountant</text>
      <text class="node-label" x="340" y="370">Trustee</text>
      <circle cx="340" cy="388" r="7" fill="var(--leaf)"/>
      <text class="node-label" x="80" y="340">Attorney</text>
      <text class="node-label" x="190" y="455">Financial</text>
      <text class="node-label" x="300" y="455" style="font-size:11px">Human Capital</text>
      <text class="node-label" x="300" y="467" style="font-size:11px">Resources</text>
      <text class="node-sub" x="300" y="478">Legacy Development</text>
      <text class="node-sub" x="300" y="486">Health Care Management</text>
      <text class="node-sub" x="300" y="494">Philanthropic Services</text>
      <text class="node-sub" x="300" y="502">Life Coaching</text>
    </svg>
  </div>
</section>

</body>
</html>
```